Carrow Facilities Services Business Card.

We need a card for Carrow Facilities Services with a new look. We also have service and supply partners that we would like to have on the card. Coatrivex is a surface application company, Carrow Facilities is a facilities services business, Bellmont Supply Co is a Facilities supply business, Prevla is a product that we use that powers our business.

```html
<!DOCTYPE html>
<html lang="en">
<head>
<meta charset="utf-8">
<title>Carrow Facilities Services – Business Card</title>
<link href="https://fonts.googleapis.com/css2?family=Montserrat:wght@500;600;700;800&family=Roboto:wght@400;500&display=swap" rel="stylesheet">
<style>
  :root {
    --blue: #1e6fc0;
    --blue-deep: #1a64b0;
    --green: #3aaa35;
    --navy: #1b2a45;
    --cyan: #27a3dc;
    --paper: #ffffff;
    --backdrop: #e9ebee;
  }
  * { box-sizing: border-box; margin: 0; padding: 0; }
  html, body { width: 1200px; height: 913px; overflow: hidden; }
  body {
    background: var(--backdrop);
    display: flex; flex-direction: column; align-items: center; justify-content: center;
    gap: 40px;
    font-family: "Roboto", Arial, sans-serif;
  }
  .card {
    position: relative;
    width: 700px; height: 400px;
    border-radius: 4px;
    box-shadow: 0 6px 18px rgba(0,0,0,.15);
    overflow: hidden;
  }
  /* Back side */
  .card-back { background: var(--blue); }
  .back-pattern {
    position: absolute; inset: 0;
    background: linear-gradient(135deg, var(--blue-deep), var(--blue) 60%, #2a7ccb);
  }
  .back-mark {
    position: absolute; left: 480px; top: 180px;
    width: 40px; height: 40px; border-radius: 50%;
    background: var(--paper);
  }
  /* Front side */
  .card-front { background: var(--paper); }
  .brand {
    position: absolute; left: 260px; top: 46px;
    display: flex; align-items: center; gap: 16px;
    color: var(--blue);
    font-family: "Montserrat", Arial, sans-serif; font-weight: 800;
  }
  .brand-dot { width: 62px; height: 62px; border-radius: 50%; background: var(--blue); }
  .brand-name { font-size: 64px; line-height: .9; letter-spacing: -1px; }
  .brand-sub { display: block; font-size: 20px; letter-spacing: 0; margin-top: 4px; }
  .edge-tab {
    position: absolute; left: 0; top: 176px;
    width: 12px; height: 44px; background: var(--green);
    border-radius: 0 3px 3px 0;
  }
  .person { position: absolute; left: 60px; top: 166px; color: var(--blue); }
  .person-name {
    font-family: "Montserrat", Arial, sans-serif; font-weight: 700;
    font-size: 28px; line-height: 1.25; letter-spacing: 1px;
  }
  .person-role {
    font-family: "Montserrat", Arial, sans-serif; font-weight: 500;
    color: var(--green); font-size: 17px; line-height: 1.2; letter-spacing: 1px; margin-top: 2px;
  }
  .address { font-size: 15px; line-height: 1.35; margin-top: 14px; }
  .rule { width: 84px; height: 3px; background: var(--green); margin: 10px 0 10px; }
  .contacts { list-style: none; font-size: 16px; line-height: 1.45; }
  .contacts li { display: flex; align-items: center; gap: 12px; }
  .contacts svg { width: 16px; height: 16px; flex: none; }
  .partners {
    position: absolute; right: 36px; top: 262px;
    display: flex; align-items: flex-end; gap: 22px;
  }
  .powered {
    border-left: 3px solid var(--green); padding-left: 12px;
    color: var(--navy); font-family: "Montserrat", Arial, sans-serif; font-weight: 700;
    white-space: nowrap;
  }
  .powered small { display: block; font-size: 9px; font-weight: 600; }
  .powered span { font-size: 22px; letter-spacing: 1px; }
  .partner {
    font-family: "Montserrat", Arial, sans-serif; font-weight: 700;
    font-size: 13px; color: var(--blue); line-height: 1.15;
    white-space: nowrap;
  }
  .partner-coat { color: var(--cyan); transform: translateY(-28px); }
</style>
</head>
<body>
  <section class="card card-back" aria-label="Card back">
    <div class="back-pattern" role="img" aria-label="Repeating faint brand-mark pattern on blue"></div>
    <div class="back-mark"></div>
  </section>

  <section class="card card-front" aria-label="Card front">
    <div class="brand">
      <div class="brand-dot"></div>
      <div class="brand-name">Carrow<span class="brand-sub">Facilities Services</span></div>
    </div>

    <div class="edge-tab"></div>

    <div class="person">
      <h1 class="person-name">DANIEL ASHWORTH</h1>
      <p class="person-role">DIRECTOR</p>
      <p class="address">48 Larkfield Road, Eastbrook,<br>EB4 (Eastbrook Station Exit B)</p>
      <div class="rule"></div>
      <ul class="contacts">
        <li>
          <svg viewBox="0 0 16 16" fill="currentColor"><path d="M3 1l3 3-2 2c1 2 3 4 6 6l2-2 3 3-2 2C7 15 1 9 1 3z"/></svg>
          0987 654 321
        </li>
        <li>
          <svg viewBox="0 0 16 16" fill="currentColor"><path d="M1 3h14v10H1z M2 4l6 5 6-5" stroke="#fff" stroke-width="1.2"/></svg>
          info@carrowfs.com
        </li>
        <li>
          <svg viewBox="0 0 16 16"><circle cx="8" cy="8" r="7" fill="currentColor"/><path d="M1 8h14M8 1c-3 4-3 10 0 14M8 1c3 4 3 10 0 14" stroke="#fff" fill="none"/></svg>
          www.carrowfs.com
        </li>
      </ul>
    </div>

    <div class="partners">
      <div class="powered"><small>Powered by</small><span>PREVLA</span></div>
      <div class="partner">Bellmont<br>Supply Co</div>
      <div class="partner partner-coat">COATRIVEX</div>
    </div>
  </section>
</body>
</html>
```